New eyelid plastic surgery office needs a business card design-Eyelid Care Partners of the Brenton

I recently used PixelForge for my logo design and was very pleased with creativity and results. It was a difficult decision for me. Now I would like to create a business card based on this logo, which I will attach.

The text should be easily legible as some of my patients have difficulty seeing, but I would like a subtle, sophisticated artistry also evident to make the card memorable. Would like the card based on a similar color scheme as the logo but the inverse or other complementary colors may prove interesting
Updates

A good question was asked...my concern about my visually impaired patients was really my desire to avoid italicized or calligraphic type fonts that may be hard to read. Standard font size for a business card would be fine. Thanks!

Thank you so much for the great work so far. I wanted to give you my particular contact information to see if that would change the look of the cards. Martin Delacourt, MD Address: 2718 Harborview Lane, Suite 206 Wilmington, NC 28517 Phone: 910-555-0193 Fax: 910-555-0194 Website: www.brentonlidstudio.example Please delete the email slot from the card. Thanks so much!

Industry/Entity Type

Plastic

```html
<!DOCTYPE html>
<html lang="en">
<head>
<meta charset="utf-8">
<title>Eyelid Care Partners of the Brenton — Business Card</title>
<link rel="stylesheet" href="https://fonts.googleapis.com/css2?family=Arimo:wght@700&display=swap">
<style>
  :root {
    --page: #ece9e6;
    --card-light: #e6e9f6;
    --card-mid: #c3cdea;
    --card-edge: #5f86c4;
    --band: #f3f5fc;
    --brand-blue: #1f4f9a;
    --ink: #111111;
    --rule: #222222;
  }
  * { box-sizing: border-box; margin: 0; padding: 0; }
  html, body {
    width: 1200px; height: 888px; overflow: hidden;
    background: var(--page);
  }
  .canvas {
    position: relative; width: 1200px; height: 888px;
    display: flex; align-items: center; justify-content: center;
  }
  .business-card {
    position: relative; width: 1050px; height: 600px; overflow: hidden;
    font-family: "Arimo", Arial, sans-serif; font-weight: 700;
    color: var(--ink);
    box-shadow: 0 6px 18px rgba(0,0,0,.18);
  }
  .card-backdrop { position: absolute; inset: 0; width: 100%; height: 100%; }
  .practice-name {
    position: absolute; left: 0; right: 0; top: 96px;
    text-align: center; color: var(--brand-blue);
    text-transform: uppercase; line-height: 1;
  }
  .practice-name .name-main { display: block; font-size: 64px; letter-spacing: 1px; }
  .practice-name .name-sub { display: block; font-size: 31px; margin-top: 12px; letter-spacing: .5px; }
  .contact-block {
    position: absolute; left: 72px; top: 378px;
    border-left: 2px solid var(--rule); padding-left: 20px;
    font-size: 22px; line-height: 30px;
  }
  .contact-heading { margin-bottom: 6px; }
  .contact-heading .colon { margin-left: 22px; }
  .doctor-name { font-size: 34px; line-height: 40px; margin: 0 0 10px 175px; }
  .detail-row { display: flex; }
  .detail-label { width: 120px; }
</style>
</head>
<body>
<main class="canvas">
  <article class="business-card">
    <svg class="card-backdrop" viewBox="0 0 1050 600" preserveAspectRatio="none">
      <defs>
        <radialGradient id="cardTone" cx="45%" cy="40%" r="80%">
          <stop offset="0" stop-color="var(--card-light)"/>
          <stop offset=".6" stop-color="var(--card-mid)"/>
          <stop offset="1" stop-color="var(--card-edge)"/>
        </radialGradient>
        <linearGradient id="bandTone" x1="0" y1="0" x2="1" y2="0">
          <stop offset="0" stop-color="var(--band)" stop-opacity=".9"/>
          <stop offset=".7" stop-color="var(--band)" stop-opacity=".5"/>
          <stop offset="1" stop-color="var(--band)" stop-opacity="0"/>
        </linearGradient>
      </defs>
      <rect width="1050" height="600" fill="url(#cardTone)" role="img" aria-label="Faint repeating eye-shape pattern across the card background"/>
      <path class="upper-arc" d="M0 150 C 300 60, 750 60, 1050 130" fill="none" stroke="var(--band)" stroke-opacity=".55" stroke-width="3"/>
      <path class="lower-band" d="M0 250 C 250 390, 650 420, 1050 250 L1050 600 L0 600 Z" fill="url(#bandTone)"/>
    </svg>

    <h1 class="practice-name">
      <span class="name-main">Eyelid Care Partners</span>
      <span class="name-sub">of the Brenton</span>
    </h1>

    <section class="contact-block">
      <p class="contact-heading">Contact<span class="colon">:</span></p>
      <p class="doctor-name">Martin Delacourt, MD</p>
      <p class="detail-row"><span class="detail-label">Address</span><span>: 2718 Harborview Lane, Suite 206 Wilmington, NC 28517</span></p>
      <p class="detail-row"><span class="detail-label">Phone</span><span>: 910 - 555 - 0193</span></p>
      <p class="detail-row"><span class="detail-label">Fax</span><span>: 910 - 555 - 0194</span></p>
      <p class="detail-row"><span class="detail-label">web</span><span>: www.brentonlidstudio.example</span></p>
    </section>
  </article>
</main>
</body>
</html>
```